Heritage Hollow Business Cards

Require a business card design. <br/><br/>Needs to include logo (either round or long version) plus these details:<br/>Maya Torvell<br/>Heritage Hollow<br/>maya@kelvadtrading.com.au<br/>02 6481 7395<br/>PO Box Glenwarra NSW 2791<br/>www.heritagehollow.com.au<br/><br/>I need in an editable format so that I can create for multiple staff members. <br/><br/>

Target Market(s)

We are an online store selling renovation products to home owners are builders. Looking for a classic classy design.

Industry/Entity Type

Home And Garden

Contact Information for Business Card

Maya Torvell
Heritage Hollow
maya@kelvadtrading.com.au
02 6481 7395
PO Box Glenwarra NSW 2791
www.heritagehollow.com.au

Colors

Designer to choose colors to be used in the design.

Requirements
Must have
• Must include Logo.

```html
<!DOCTYPE html>
<html lang="en">
<head>
<meta charset="utf-8">
<title>Heritage Hollow Business Cards</title>
<link href="https://fonts.googleapis.com/css2?family=Lato:wght@400;700;900&display=swap" rel="stylesheet">
<style>
  :root {
    --backdrop: #3b3430;
    --card: #050505;
    --ink: #ffffff;
    --ink-soft: #e6e6e6;
    --emboss: #1c1c1c;
    --rule: #d9d9d9;
  }
  * { box-sizing: border-box; margin: 0; padding: 0; }
  html, body { width: 1200px; height: 847px; overflow: hidden; }
  body {
    background: var(--backdrop);
    font-family: "Lato", sans-serif;
    display: flex;
    align-items: center;
    justify-content: center;
    gap: 40px;
  }
  .card {
    width: 540px;
    height: 310px;
    background: var(--card);
    position: relative;
    box-shadow: 0 8px 24px rgba(0,0,0,.45);
  }
  /* Front */
  .card--front { display: flex; align-items: center; justify-content: center; }
  .front-mark {
    display: flex; align-items: center; gap: 22px;
  }
  .front-mark__circle {
    width: 110px; height: 110px; border-radius: 50%;
    border: 2px solid var(--emboss);
  }
  .front-mark__name {
    color: var(--emboss);
    font-weight: 700;
    font-size: 46px;
    line-height: 1;
    width: 250px;
  }
  /* Back */
  .card--back { display: flex; align-items: center; padding: 0 36px 0 40px; }
  .brand {
    width: 170px; height: 170px; border-radius: 50%;
    border: 1.5px solid var(--ink);
    display: flex; align-items: center; justify-content: center;
    text-align: center;
    color: var(--ink);
    font-weight: 700;
    font-size: 26px;
    line-height: 1.05;
    flex-shrink: 0;
  }
  .divider {
    width: 1.5px; height: 200px; background: var(--rule);
    margin: 0 28px 0 34px; flex-shrink: 0;
  }
  .contact { color: var(--ink-soft); font-size: 14.5px; line-height: 1.35; }
  .contact__name { color: var(--ink); font-weight: 900; font-size: 24px; margin-bottom: 4px; }
  .contact__address { margin-bottom: 6px; }
  .contact__row { display: flex; align-items: center; gap: 10px; }
  .contact__row svg { width: 14px; height: 14px; flex-shrink: 0; }
  .contact__web { padding-left: 24px; }
</style>
</head>
<body>
  <section class="card card--front" aria-label="Card front">
    <div class="front-mark">
      <span class="front-mark__circle"></span>
      <span class="front-mark__name">Heritage Hollow</span>
    </div>
  </section>

  <section class="card card--back" aria-label="Card back">
    <div class="brand">Heritage<br>Hollow</div>
    <span class="divider"></span>
    <div class="contact">
      <p class="contact__name">Maya Torvell</p>
      <p>Heritage Hollow</p>
      <p class="contact__address">PO Box Glenwarra<br>NSW 2791</p>
      <p class="contact__row">
        <svg viewBox="0 0 16 16" aria-hidden="true"><path fill="#fff" d="M3.5 1.5l2.5 0 1 3.5-1.7 1.2a8 8 0 0 0 4.5 4.5L11 9l3.5 1v2.5c0 1-1 2-2 2C6.5 14.5 1.5 9.5 1.5 3.5c0-1 1-2 2-2z"/></svg>
        <span>02 6481 7395</span>
      </p>
      <p class="contact__row">
        <svg viewBox="0 0 16 16" aria-hidden="true"><rect x="1" y="3" width="14" height="10" fill="#fff"/><path d="M1 3l7 6 7-6" stroke="#000" stroke-width="1.3" fill="none"/></svg>
        <span>maya@kelvadtrading.com.au</span>
      </p>
      <p class="contact__row">
        <svg viewBox="0 0 16 16" aria-hidden="true"><circle cx="8" cy="8" r="7" fill="#fff"/><path d="M1 8h14M8 1c-3 3.5-3 10.5 0 14M8 1c3 3.5 3 10.5 0 14" stroke="#000" stroke-width="1" fill="none"/></svg>
        <span>www.heritagehollow.com.au</span>
      </p>
    </div>
  </section>
</body>
</html>
```